Ledgerwise Forge - WordPress Theme & Logo

Design a logo and Wordpress website design for Ledgerwise Forge. Ledgerwise Forge provides cryptocurrency development services to clients who need a team to create & continue developing a new cryptocurrency or who want to replace their current cryptocurrency development team. more details in the attached document.
Updates

Target Market(s)

Entrepreneurs who are building a business / platform that makes use of an underlying cryptocurrency.

Logo Text

LF or Ledgerwise Forge

Coding

Coded - Design and coding required

Font styles to use
Sans Serif

Requirements
Must have
• Professional logo, complete coded Wordpress theme for all pages, containing all specified links and buttons
Nice to have
• It would be nice if the buttons that are meant to integrate with Dealtrail contain the necessary code for that. I can provide any necessary Dealtrail details from my account.
Should not have
• Slow loading time

```html
<!DOCTYPE html>
<html lang="en">
<head>
<meta charset="utf-8">
<title>Ledgerwise Forge – Home Page Layouts</title>
<link href="https://fonts.googleapis.com/css2?family=Roboto:wght@300;400;500;700;900&display=swap" rel="stylesheet">
<style>
:root{
  --blue:#1466c2;
  --blue-dark:#0d4f9e;
  --blue-deep:#0a3f86;
  --navy:#0b1124;
  --ink:#121212;
  --muted:#4a4a4a;
  --soft:#8a8a8a;
  --pale:#eef4fb;
  --stage:#f6f6f6;
  --white:#ffffff;
}
*{margin:0;padding:0;box-sizing:border-box}
html,body{width:795px;height:1200px;overflow:hidden;background:var(--stage);font-family:'Roboto',Arial,sans-serif;color:var(--ink)}
.board{position:absolute;left:0;top:0;width:1568px;height:2367px;transform:scale(0.50702);transform-origin:0 0}
.page{position:absolute;top:69px;width:670px;height:2228px;background:var(--white);overflow:hidden;box-shadow:0 0 6px rgba(0,0,0,.08)}
.page--a{left:81px}
.page--b{left:818px}

.topbar{height:3px;background:var(--blue)}
.header{height:55px;position:relative}
.brand{position:absolute;left:64px;top:14px;display:flex;align-items:center;gap:7px}
.brand__mark{width:26px;height:26px;background:var(--blue)}
.brand__name{font-size:9px;font-weight:700;line-height:10px;color:var(--ink);text-transform:uppercase}
.contact{position:absolute;top:19px;display:flex;gap:8px;align-items:flex-start}
.contact--phone{left:345px}
.contact--mail{left:464px}
.contact svg{width:20px;height:20px;margin-top:1px}
.contact__label{font-size:8px;font-weight:700;line-height:11px}
.contact__value{font-size:8.5px;color:var(--muted);line-height:12px}

.nav{height:31px;background:var(--blue);position:relative;display:flex;align-items:center;padding-left:34px;gap:0}
.nav a{color:var(--white);font-size:8.5px;font-weight:500;text-decoration:none;margin-right:23px}
.nav__search{position:absolute;right:6px;top:3px;width:152px;height:25px;background:var(--blue-dark);clip-path:polygon(10px 0,100% 0,100% 100%,0 100%);display:flex;align-items:center;padding-left:22px;color:var(--white);font-size:8.5px;font-weight:500}
.nav__slash{position:absolute;right:151px;top:0;width:3px;height:31px;background:var(--white);transform:skewX(-22deg)}
.nav__btn{position:absolute;right:6px;top:4px;width:17px;height:17px;background:var(--blue);display:flex;align-items:center;justify-content:center}

.hero{position:relative;height:342px}
.hero__edge{position:absolute;inset:0;background:var(--blue);clip-path:polygon(0 0,100% 0,100% 86%,50% 100%,0 86%)}
.hero__media{position:absolute;inset:0 0 5px 0;clip-path:polygon(0 0,100% 0,100% 86.5%,50% 100%,0 86.5%)}
.hero--city .hero__media{background:radial-gradient(ellipse at 50% 75%,#1b7bd8 0%,#0c3a86 40%,#061a48 75%),#061a48}
.hero--cubes .hero__media{background:radial-gradient(ellipse at 60% 20%,#b592c9 0%,#5a4a98 35%,#1d1f5c 70%,#0e1140 100%)}
.hero__title{position:absolute;top:108px;width:100%;text-align:center;color:var(--white);font-size:28px;font-weight:700;letter-spacing:.2px}
.hero__sub{position:absolute;top:157px;width:100%;text-align:center;color:var(--white);font-size:11px;font-weight:400}
.hero__actions{position:absolute;top:196px;width:100%;display:flex;justify-content:center;gap:7px}
.hero__arrow{position:absolute;top:158px;width:18px;height:18px;border-radius:50%;background:var(--white);display:flex;align-items:center;justify-content:center}
.hero__arrow--prev{left:19px}
.hero__arrow--next{right:19px}

.btn{display:inline-flex;align-items:center;gap:6px;height:25px;padding:0 11px;background:var(--blue);color:var(--white);font-size:8px;font-weight:700;text-transform:uppercase;border-radius:1px}
.btn svg{width:8px;height:8px}

.section-title{text-align:center;font-size:20px;font-weight:700;text-transform:uppercase}
.rule{width:36px;height:2px;background:var(--blue);margin:8px auto 0}
.rule--light{background:var(--white)}
.rule--left{margin-left:0}

.welcome{height:225px;padding-top:43px;text-align:center}
.welcome__text{width:392px;margin:16px auto 0;font-size:8.5px;line-height:14.5px;color:var(--muted);font-weight:300}
.welcome .btn{margin-top:20px}

.why{height:276px;background:radial-gradient(ellipse at 30% 60%,#2a7fd6 0%,#1466c2 45%,#0e56aa 100%);padding-top:33px}
.why .section-title{color:var(--white)}
.why__cards{display:flex;gap:19px;margin:30px 0 0 94px}
.feature{width:148px;height:138px;background:var(--white);text-align:center;padding-top:18px}
.feature__icon{width:50px;height:48px;margin:0 auto}
.feature__title{font-size:8.5px;font-weight:700;margin-top:19px;text-transform:uppercase}
.feature__text{font-size:8px;line-height:12px;color:var(--muted);margin:9px auto 0;width:122px}

.about{height:267px;position:relative}
.about__photo{position:absolute;left:74px;top:39px;width:187px;height:180px;box-shadow:6px 6px 0 var(--blue);background:linear-gradient(135deg,#2b3a4c 0%,#6f8496 45%,#c9d6de 70%,#4a5b6c 100%)}
.about__body{position:absolute;left:312px;top:44px;width:292px}
.about__title{font-size:20px;font-weight:700;text-transform:uppercase}
.about__text{font-size:8.3px;line-height:16.8px;color:var(--muted);font-weight:300;margin-top:14px}
.about .btn{margin-top:14px}

.testimonials{height:252px;background:radial-gradient(ellipse at 50% 40%,#1b6fcb 0%,#1261bb 55%,#0c52a4 100%);padding-top:27px;position:relative}
.testimonials .section-title{color:var(--white)}
.testimonials__cards{position:absolute;left:94px;top:107px;display:flex;gap:28px}
.quote{width:142px;height:113px;background:var(--white);text-align:center;position:relative;padding-top:31px}
.quote__avatar{position:absolute;left:50%;top:-20px;margin-left:-20px;width:40px;height:40px;border-radius:50%;border:2px solid var(--white);background:linear-gradient(160deg,#c9b9a8,#7d6a5c);box-shadow:0 1px 3px rgba(0,0,0,.2)}
.quote__name{font-size:8.5px;font-weight:700;color:var(--blue)}
.quote__lead{font-size:8.5px;margin-top:5px}
.quote__text{font-size:7.6px;line-height:11.5px;color:var(--soft);margin:6px auto 0;width:122px;font-weight:300}
.testimonials__chev{position:absolute;top:146px}
.testimonials__chev--prev{left:37px}
.testimonials__chev--next{right:37px}

.services{height:353px;padding-top:43px;position:relative}
.services__cards{position:absolute;left:69px;top:107px;display:flex;gap:25px}
.offer{width:157px;height:198px;background:var(--white);box-shadow:0 0 5px rgba(0,0,0,.12);padding-top:15px}
.offer__icon{width:70px;height:66px;margin:0 auto;display:block}
.offer__title{text-align:center;font-size:7.8px;font-weight:700;margin-top:14px;text-transform:uppercase}
.offer__list{list-style:none;margin:8px 0 0 23px}
.offer__list li{display:flex;align-items:center;gap:6px;font-size:8px;color:var(--muted);height:20px}
.offer__list svg{width:7px;height:7px;flex:none}
.offer__more{text-align:center;font-size:8px;font-weight:500;color:var(--blue);margin-top:5px;display:flex;justify-content:center;align-items:center;gap:4px}
.offer__more svg{width:7px;height:7px}

.cta{height:207px;background:var(--pale);padding-top:24px;text-align:center}
.cta__text{width:420px;margin:15px auto 0;font-size:8.5px;line-height:14.5px;color:var(--muted);font-weight:300}
.cta .btn{margin-top:17px}

.footer{position:relative;height:217px}
.footer__edge{position:absolute;inset:0;background:var(--blue);clip-path:polygon(0 50px,50% 0,100% 50px,100% 100%,0 100%)}
.footer__body{position:absolute;inset:4px 0 0 0;background:linear-gradient(180deg,#0d1630 0%,#070b18 100%);clip-path:polygon(0 50px,50% 0,100% 50px,100% 100%,0 100%);color:var(--white)}
.footer .brand{left:62px;top:64px}
.footer .brand__name{color:var(--white)}
.footer__about{position:absolute;left:62px;top:105px;width:150px;font-size:8.5px;line-height:14px;font-weight:300}
.footer__col{position:absolute;top:55px}
.footer__col--quick{left:252px}
.footer__col--other{left:405px}
.footer__col--news{left:492px}
.footer__heading{font-size:8px;font-weight:700;margin-bottom:10px}
.footer__col a{display:block;color:var(--white);text-decoration:none;font-size:8px;font-weight:300;line-height:19.2px}
.footer__input{width:115px;height:21px;background:var(--white);color:var(--muted);font-size:7px;padding:6px 6px;margin-top:3px}
.footer__subscribe{margin-top:15px;width:72px;height:20px;background:var(--blue);font-size:7.5px;font-weight:700;display:flex;align-items:center;justify-content:center;text-transform:uppercase}
.footer__social{display:flex;gap:13px;margin-top:17px}
.footer__social span{width:6px;height:6px;border-radius:50%;background:var(--white)}
.footer__line{position:absolute;left:60px;right:65px;top:181px;height:1px;background:rgba(255,255,255,.25)}
.footer__copy{position:absolute;top:195px;width:100%;text-align:center;font-size:8px;font-weight:300}
</style>
</head>
<body>
<div class="board">

  <!-- Layout A -->
  <div class="page page--a">
    <div class="topbar"></div>
    <header class="header">
      <div class="brand"><span class="brand__mark"></span><span class="brand__name">Ledgerwise<br>Forge</span></div>
      <div class="contact contact--phone">
        <svg viewBox="0 0 20 20"><circle cx="10" cy="10" r="8.5" fill="none" stroke="#1466c2" stroke-width="1.4"/><path d="M7 5.5l2 2-1 1.3c.6 1.4 1.7 2.5 3.2 3.2l1.3-1 2 2-1.2 1.4c-3.7-.6-6.6-3.5-7.2-7.2z" fill="#1466c2"/></svg>
        <div><div class="contact__label">Phone</div><div class="contact__value">123 (4568) 789</div></div>
      </div>
      <div class="contact contact--mail">
        <svg viewBox="0 0 20 20"><rect x="2" y="5" width="16" height="11" fill="none" stroke="#1466c2" stroke-width="1.4"/><path d="M2 5l8 6 8-6M2 16l6-5M18 16l-6-5" fill="none" stroke="#1466c2" stroke-width="1.2"/></svg>
        <div><div class="contact__label">Email</div><div class="contact__value">info@ledgerwiseforge.com</div></div>
      </div>
    </header>
    <nav class="nav">
      <a>Home</a><a>Services</a><a>About Us</a><a>Ledgerwise Forge Method</a><a>Testimonials</a><a>Blog</a><a>Contact Us</a>
      <span class="nav__slash"></span>
      <div class="nav__search">Search<span class="nav__btn"><svg width="8" height="8" viewBox="0 0 8 8"><circle cx="3.3" cy="3.3" r="2.4" fill="none" stroke="#fff" stroke-width="1.2"/><path d="M5 5l2.3 2.3" stroke="#fff" stroke-width="1.3"/></svg></span></div>
    </nav>
    <section class="hero hero--city">
      <div class="hero__edge"></div>
      <div class="hero__media" role="img" aria-label="Night city skyline with a glowing network grid and a person standing on a lit platform"></div>
      <h1 class="hero__title">LEDGERWISE FORGE</h1>
      <p class="hero__sub">Your own cryptocurrency. Secure, easy to use, and built by an expert team.</p>
      <div class="hero__actions">
        <span class="btn">Get Stared <svg viewBox="0 0 8 8"><circle cx="4" cy="4" r="4" fill="#fff"/><path d="M3.2 2.3L5 4 3.2 5.7" fill="none" stroke="#1466c2" stroke-width="1.1"/></svg></span>
        <span class="btn">Schedule Free Consultation <svg viewBox="0 0 8 8"><circle cx="4" cy="4" r="4" fill="#fff"/><path d="M3.2 2.3L5 4 3.2 5.7" fill="none" stroke="#1466c2" stroke-width="1.1"/></svg></span>
      </div>
      <span class="hero__arrow hero__arrow--prev"><svg width="8" height="8" viewBox="0 0 8 8"><path d="M5.2 1.2L2.4 4l2.8 2.8" fill="none" stroke="#1466c2" stroke-width="1.6"/></svg></span>
      <span class="hero__arrow hero__arrow--next"><svg width="8" height="8" viewBox="0 0 8 8"><path d="M2.8 1.2L5.6 4 2.8 6.8" fill="none" stroke="#1466c2" stroke-width="1.6"/></svg></span>
    </section>
    <section class="welcome">
      <h2 class="section-title">Welcome To</h2><div class="rule"></div>
      <p class="welcome__text">Ledgerwise Forge adds professionalism to cryptocurrency development. Our done-for-you service covers everything from development and IT operations to ongoing support. You have access to a full team, for less than the typical cost of a single developer.</p>
      <span class="btn">Learn More <svg viewBox="0 0 8 8"><circle cx="4" cy="4" r="4" fill="#fff"/><path d="M3.2 2.3L5 4 3.2 5.7" fill="none" stroke="#1466c2" stroke-width="1.1"/></svg></span>
    </section>
    <section class="why">
      <h2 class="section-title">Why Choose Ledgerwise Forge</h2><div class="rule rule--light"></div>
      <div class="why__cards">
        <div class="feature"><svg class="feature__icon" viewBox="0 0 50 48"><path d="M6 4v36h40" fill="none" stroke="#1466c2" stroke-width="3"/><rect x="12" y="24" width="6" height="14" fill="#1466c2"/><rect x="21" y="16" width="6" height="22" fill="#1466c2"/><rect x="30" y="20" width="6" height="18" fill="#1466c2"/><circle cx="36" cy="14" r="7" fill="none" stroke="#1466c2" stroke-width="2.5"/></svg><div class="feature__title">Value</div><p class="feature__text">A team of experts, regular updates, and fixed costs</p></div>
        <div class="feature"><svg class="feature__icon" viewBox="0 0 50 48" role="img" aria-label="Handshake icon"><path d="M8 26l14-18 20 14-14 20z" fill="#1466c2"/></svg><div class="feature__title">Support</div><p class="feature__text">Receive advice and other services, beyond development.</p></div>
        <div class="feature"><svg class="feature__icon" viewBox="0 0 50 48" role="img" aria-label="Globe with handshake icon"><circle cx="25" cy="18" r="13" fill="#1466c2"/><rect x="6" y="32" width="38" height="8" fill="#1466c2"/></svg><div class="feature__title">Commitment</div><p class="feature__text">Enjoy regular updates and new features.</p></div>
      </div>
    </section>
    <section class="about">
      <div class="about__photo" role="img" aria-label="Two colleagues reviewing a tablet in a server room"></div>
      <div class="about__body">
        <h2 class="about__title">About Us</h2><div class="rule rule--left"></div>
        <p class="about__text">In addition to creating and enhancing cryptocurrencies for clients, the Ledgerwise Forge team has been running the Corvex cryptocurrency since 2017. We prefer long-term relationships, enabling us to deliver the very highest quality and giving you peace of mind that you've got a professional and trustworthy team at your side.</p>
        <span class="btn">Learn More <svg viewBox="0 0 8 8"><circle cx="4" cy="4" r="4" fill="#fff"/><path d="M3.2 2.3L5 4 3.2 5.7" fill="none" stroke="#1466c2" stroke-width="1.1"/></svg></span>
      </div>
    </section>
    <section class="testimonials">
      <h2 class="section-title">Client Testimonials</h2><div class="rule rule--light"></div>
      <div class="testimonials__cards">
        <div class="quote"><span class="quote__avatar" role="img" aria-label="Client portrait"></span><div class="quote__name">Marla Venturo</div><div class="quote__lead">Lorem ipsum dolor  amet</div><p class="quote__text">Lorem consectetur adipiscing elit, sed do emod tempor labore admin dolore magna.</p></div>
        <div class="quote"><span class="quote__avatar" role="img" aria-label="Client portrait"></span><div class="quote__name">Willam smith</div><div class="quote__lead">Lorem ipsum dolor  amet</div><p class="quote__text">Lorem consectetur adipiscing elit, sed do emod tempor labore admin dolore magna.</p></div>
        <div class="quote"><span class="quote__avatar" role="img" aria-label="Client portrait"></span><div class="quote__name">Jhon smith</div><div class="quote__lead">Lorem ipsum dolor  amet</div><p class="quote__text">Lorem consectetur adipiscing elit, sed do emod tempor labore admin dolore magna.</p></div>
      </div>
      <svg class="testimonials__chev testimonials__chev--prev" width="8" height="12" viewBox="0 0 8 12"><path d="M6 1L1.5 6 6 11" fill="none" stroke="#fff" stroke-width="1.5"/></svg>
      <svg class="testimonials__chev testimonials__chev--next" width="8" height="12" viewBox="0 0 8 12"><path d="M2 1l4.5 5L2 11" fill="none" stroke="#fff" stroke-width="1.5"/></svg>
    </section>
    <section class="services">
      <h2 class="section-title">Our Services</h2><div class="rule"></div>
      <div class="services__cards">
        <div class="offer"><svg class="offer__icon" viewBox="0 0 70 66" role="img" aria-label="Hand holding a discount badge icon"><circle cx="40" cy="18" r="14" fill="#1466c2"/><rect x="8" y="38" width="10" height="22" fill="#1466c2"/><path d="M20 42h22l16-8-6 18-32 8z" fill="#1466c2"/></svg><div class="offer__title">Basic Offering</div>
          <ul class="offer__list"><li><svg viewBox="0 0 8 8"><circle cx="4" cy="4" r="4" fill="#1466c2"/><path d="M2.2 4.1l1.3 1.3 2.4-2.6" fill="none" stroke="#fff" stroke-width="1"/></svg>Lower cost per month</li><li><svg viewBox="0 0 8 8"><circle cx="4" cy="4" r="4" fill="#1466c2"/><path d="M2.2 4.1l1.3 1.3 2.4-2.6" fill="none" stroke="#fff" stroke-width="1"/></svg>Slower release schedule</li><li><svg viewBox="0 0 8 8"><circle cx="4" cy="4" r="4" fill="#1466c2"/><path d="M2.2 4.1l1.3 1.3 2.4-2.6" fill="none" stroke="#fff" stroke-width="1"/></svg>Limited support hours</li></ul>
          <div class="offer__more">Read More <svg viewBox="0 0 8 8"><circle cx="4" cy="4" r="4" fill="#1466c2"/><path d="M3.2 2.3L5 4 3.2 5.7" fill="none" stroke="#fff" stroke-width="1.1"/></svg></div></div>
        <div class="offer"><svg class="offer__icon" viewBox="0 0 70 66" role="img" aria-label="Hand holding a box with tools icon"><rect x="26" y="6" width="18" height="14" fill="#1466c2"/><rect x="22" y="24" width="30" height="26" fill="#1466c2"/><rect x="8" y="38" width="10" height="22" fill="#1466c2"/><path d="M20 52h34l8-10v14H20z" fill="#1466c2"/></svg><div class="offer__title">Full Service Offering</div>
          <ul class="offer__list"><li><svg viewBox="0 0 8 8"><circle cx="4" cy="4" r="4" fill="#1466c2"/><path d="M2.2 4.1l1.3 1.3 2.4-2.6" fill="none" stroke="#fff" stroke-width="1"/></svg>Mid-range cost per month</li><li><svg viewBox="0 0 8 8"><circle cx="4" cy="4" r="4" fill="#1466c2"/><path d="M2.2 4.1l1.3 1.3 2.4-2.6" fill="none" stroke="#fff" stroke-width="1"/></svg>Releases every 1.5 - 2 months</li><li><svg viewBox="0 0 8 8"><circle cx="4" cy="4" r="4" fill="#1466c2"/><path d="M2.2 4.1l1.3 1.3 2.4-2.6" fill="none" stroke="#fff" stroke-width="1"/></svg>Client can help request</li></ul>
          <div class="offer__more">Read More <svg viewBox="0 0 8 8"><circle cx="4" cy="4" r="4" fill="#1466c2"/><path d="M3.2 2.3L5 4 3.2 5.7" fill="none" stroke="#fff" stroke-width="1.1"/></svg></div></div>
        <div class="offer"><svg class="offer__icon" viewBox="0 0 70 66" role="img" aria-label="Hand holding a crown with people icon"><circle cx="20" cy="14" r="5" fill="#1466c2"/><circle cx="35" cy="8" r="5" fill="#1466c2"/><circle cx="50" cy="14" r="5" fill="#1466c2"/><path d="M22 24l6 6 7-8 7 8 6-6v14H22z" fill="#1466c2"/><path d="M8 52l18-8h30l6-4-12 18H18z" fill="#1466c2"/></svg><div class="offer__title">Premium Service</div>
          <ul class="offer__list"><li><svg viewBox="0 0 8 8"><circle cx="4" cy="4" r="4" fill="#1466c2"/><path d="M2.2 4.1l1.3 1.3 2.4-2.6" fill="none" stroke="#fff" stroke-width="1"/></svg>Higher cost per month</li><li><svg viewBox="0 0 8 8"><circle cx="4" cy="4" r="4" fill="#1466c2"/><path d="M2.2 4.1l1.3 1.3 2.4-2.6" fill="none" stroke="#fff" stroke-width="1"/></svg>Priority 24/7 support</li><li><svg viewBox="0 0 8 8"><circle cx="4" cy="4" r="4" fill="#1466c2"/><path d="M2.2 4.1l1.3 1.3 2.4-2.6" fill="none" stroke="#fff" stroke-width="1"/></svg>Dedicated development lead</li></ul>
          <div class="offer__more">Read More <svg viewBox="0 0 8 8"><circle cx="4" cy="4" r="4" fill="#1466c2"/><path d="M3.2 2.3L5 4 3.2 5.7" fill="none" stroke="#fff" stroke-width="1.1"/></svg></div></div>
      </div>
    </section>
    <section class="cta">
      <h2 class="section-title">Lorem Ipsum Dolor</h2><div class="rule"></div>
      <p class="cta__text">Lorem ipsum dolor sit amet, consectetur adipiscing elit, sed do eiusmod tempor incididunt ut labore et dolore magna aliqua. Ut enim ad minim veniam, quis nostrud exercitation ullamco laboris nisi ut aliquip ex ea commodo consequat. Duis aute irure dolor in reprehenderit in voluptate velit esse cillum dolore fugiat nulla pariatur. Excepteur sint occaecat cupidatat non proident, sunt in culpa qui officia</p>
      <span class="btn">Schedule Free Consultation <svg viewBox="0 0 8 8"><circle cx="4" cy="4" r="4" fill="#fff"/><path d="M3.2 2.3L5 4 3.2 5.7" fill="none" stroke="#1466c2" stroke-width="1.1"/></svg></span>
    </section>
    <footer class="footer">
      <div class="footer__edge"></div>
      <div class="footer__body">
        <div class="brand"><span class="brand__mark"></span><span class="brand__name">Ledgerwise<br>Forge</span></div>
        <p class="footer__about">Ledgerwise Forge adds professionalism to cryptocurrency development.</p>
        <div class="footer__col footer__col--quick"><div class="footer__heading">Quicklinks</div><a>Services</a><a>Ledgerwise Forge Method</a><a>Testimonials</a><a>Blog</a><a>About Us</a></div>
        <div class="footer__col footer__col--other"><div class="footer__heading">Qtherlinks</div><a>Blog</a><a>privacy</a><a>Services</a><a>Team</a></div>
        <div class="footer__col footer__col--news"><div class="footer__heading">Get our Newsletter</div><div class="footer__input">Enter Email:</div><div class="footer__subscribe">Subscribe</div><div class="footer__social"><span></span><span></span><span></span><span></span><span></span></div></div>
        <div class="footer__line"></div>
        <div class="footer__copy">©Copyrights 2021 &nbsp; Ledgerwise Forge &nbsp;| &nbsp; All Rights Reserved &nbsp;|</div>
      </div>
    </footer>
  </div>

  <!-- Layout B -->
  <div class="page page--b">
    <div class="topbar"></div>
    <header class="header">
      <div class="brand"><span class="brand__mark"></span><span class="brand__name">Ledgerwise<br>Forge</span></div>
      <div class="contact contact--phone">
        <svg viewBox="0 0 20 20"><circle cx="10" cy="10" r="8.5" fill="none" stroke="#1466c2" stroke-width="1.4"/><path d="M7 5.5l2 2-1 1.3c.6 1.4 1.7 2.5 3.2 3.2l1.3-1 2 2-1.2 1.4c-3.7-.6-6.6-3.5-7.2-7.2z" fill="#1466c2"/></svg>
        <div><div class="contact__label">Phone</div><div class="contact__value">123 (4568) 789</div></div>
      </div>
      <div class="contact contact--mail">
        <svg viewBox="0 0 20 20"><rect x="2" y="5" width="16" height="11" fill="none" stroke="#1466c2" stroke-width="1.4"/><path d="M2 5l8 6 8-6M2 16l6-5M18 16l-6-5" fill="none" stroke="#1466c2" stroke-width="1.2"/></svg>
        <div><div class="contact__label">Email</div><div class="contact__value">info@ledgerwiseforge.com</div></div>
      </div>
    </header>
    <nav class="nav">
      <a>Home</a><a>Services</a><a>About Us</a><a>Ledgerwise Forge Method</a><a>Testimonials</a><a>Blog</a><a>Contact Us</a>
      <span class="nav__slash"></span>
      <div class="nav__search">Search<span class="nav__btn"><svg width="8" height="8" viewBox="0 0 8 8"><circle cx="3.3" cy="3.3" r="2.4" fill="none" stroke="#fff" stroke-width="1.2"/><path d="M5 5l2.3 2.3" stroke="#fff" stroke-width="1.3"/></svg></span></div>
    </nav>
    <section class="hero hero--cubes">
      <div class="hero__edge"></div>
      <div class="hero__media" role="img" aria-label="Floating glass cubes joined by glowing edges on a violet background"></div>
      <h1 class="hero__title">LEDGERWISE FORGE</h1>
      <p class="hero__sub">Your own cryptocurrency. Secure, easy to use, and built by an expert team.</p>
      <div class="hero__actions">
        <span class="btn">Get Stared <svg viewBox="0 0 8 8"><circle cx="4" cy="4" r="4" fill="#fff"/><path d="M3.2 2.3L5 4 3.2 5.7" fill="none" stroke="#1466c2" stroke-width="1.1"/></svg></span>
        <span class="btn">Schedule Free Consultation <svg viewBox="0 0 8 8"><circle cx="4" cy="4" r="4" fill="#fff"/><path d="M3.2 2.3L5 4 3.2 5.7" fill="none" stroke="#1466c2" stroke-width="1.1"/></svg></span>
      </div>
      <span class="hero__arrow hero__arrow--prev"><svg width="8" height="8" viewBox="0 0 8 8"><path d="M5.2 1.2L2.4 4l2.8 2.8" fill="none" stroke="#1466c2" stroke-width="1.6"/></svg></span>
      <span class="hero__arrow hero__arrow--next"><svg width="8" height="8" viewBox="0 0 8 8"><path d="M2.8 1.2L5.6 4 2.8 6.8" fill="none" stroke="#1466c2" stroke-width="1.6"/></svg></span>
    </section>
    <section class="welcome">
      <h2 class="section-title">Welcome To</h2><div class="rule"></div>
      <p class="welcome__text">Ledgerwise Forge adds professionalism to cryptocurrency development. Our done-for-you service covers everything from development and IT operations to ongoing support. You have access to a full team, for less than the typical cost of a single developer.</p>
      <span class="btn">Learn More <svg viewBox="0 0 8 8"><circle cx="4" cy="4" r="4" fill="#fff"/><path d="M3.2 2.3L5 4 3.2 5.7" fill="none" stroke="#1466c2" stroke-width="1.1"/></svg></span>
    </section>
    <section class="why">
      <h2 class="section-title">Why Choose Ledgerwise Forge</h2><div class="rule rule--light"></div>
      <div class="why__cards">
        <div class="feature"><svg class="feature__icon" viewBox="0 0 50 48"><path d="M6 4v36h40" fill="none" stroke="#1466c2" stroke-width="3"/><rect x="12" y="24" width="6" height="14" fill="#1466c2"/><rect x="21" y="16" width="6" height="22" fill="#1466c2"/><rect x="30" y="20" width="6" height="18" fill="#1466c2"/><circle cx="36" cy="14" r="7" fill="none" stroke="#1466c2" stroke-width="2.5"/></svg><div class="feature__title">Value</div><p class="feature__text">A team of experts, regular updates, and fixed costs</p></div>
        <div class="feature"><svg class="feature__icon" viewBox="0 0 50 48" role="img" aria-label="Handshake icon"><path d="M8 26l14-18 20 14-14 20z" fill="#1466c2"/></svg><div class="feature__title">Support</div><p class="feature__text">Receive advice and other services, beyond development.</p></div>
        <div class="feature"><svg class="feature__icon" viewBox="0 0 50 48" role="img" aria-label="Globe with handshake icon"><circle cx="25" cy="18" r="13" fill="#1466c2"/><rect x="6" y="32" width="38" height="8" fill="#1466c2"/></svg><div class="feature__title">Commitment</div><p class="feature__text">Enjoy regular updates and new features.</p></div>
      </div>
    </section>
    <section class="about">
      <div class="about__photo" role="img" aria-label="Two colleagues reviewing a tablet in a server room"></div>
      <div class="about__body">
        <h2 class="about__title">About Us</h2><div class="rule rule--left"></div>
        <p class="about__text">In addition to creating and enhancing cryptocurrencies for clients, the Ledgerwise Forge team has been running the Corvex cryptocurrency since 2017. We prefer long-term relationships, enabling us to deliver the very highest quality and giving you peace of mind that you've got a professional and trustworthy team at your side.</p>
        <span class="btn">Learn More <svg viewBox="0 0 8 8"><circle cx="4" cy="4" r="4" fill="#fff"/><path d="M3.2 2.3L5 4 3.2 5.7" fill="none" stroke="#1466c2" stroke-width="1.1"/></svg></span>
      </div>
    </section>
    <section class="testimonials">
      <h2 class="section-title">Client Testimonials</h2><div class="rule rule--light"></div>
      <div class="testimonials__cards">
        <div class="quote"><span class="quote__avatar" role="img" aria-label="Client portrait"></span><div class="quote__name">Marla Venturo</div><div class="quote__lead">Lorem ipsum dolor  amet</div><p class="quote__text">Lorem consectetur adipiscing elit, sed do emod tempor labore admin dolore magna.</p></div>
        <div class="quote"><span class="quote__avatar" role="img" aria-label="Client portrait"></span><div class="quote__name">Willam smith</div><div class="quote__lead">Lorem ipsum dolor  amet</div><p class="quote__text">Lorem consectetur adipiscing elit, sed do emod tempor labore admin dolore magna.</p></div>
        <div class="quote"><span class="quote__avatar" role="img" aria-label="Client portrait"></span><div class="quote__name">Jhon smith</div><div class="quote__lead">Lorem ipsum dolor  amet</div><p class="quote__text">Lorem consectetur adipiscing elit, sed do emod tempor labore admin dolore magna.</p></div>
      </div>
      <svg class="testimonials__chev testimonials__chev--prev" width="8" height="12" viewBox="0 0 8 12"><path d="M6 1L1.5 6 6 11" fill="none" stroke="#fff" stroke-width="1.5"/></svg>
      <svg class="testimonials__chev testimonials__chev--next" width="8" height="12" viewBox="0 0 8 12"><path d="M2 1l4.5 5L2 11" fill="none" stroke="#fff" stroke-width="1.5"/></svg>
    </section>
    <section class="services">
      <h2 class="section-title">Our Services</h2><div class="rule"></div>
      <div class="services__cards">
        <div class="offer"><svg class="offer__icon" viewBox="0 0 70 66" role="img" aria-label="Hand holding a discount badge icon"><circle cx="40" cy="18" r="14" fill="#1466c2"/><rect x="8" y="38" width="10" height="22" fill="#1466c2"/><path d="M20 42h22l16-8-6 18-32 8z" fill="#1466c2"/></svg><div class="offer__title">Basic Offering</div>
          <ul class="offer__list"><li><svg viewBox="0 0 8 8"><circle cx="4" cy="4" r="4" fill="#1466c2"/><path d="M2.2 4.1l1.3 1.3 2.4-2.6" fill="none" stroke="#fff" stroke-width="1"/></svg>Lower cost per month</li><li><svg viewBox="0 0 8 8"><circle cx="4" cy="4" r="4" fill="#1466c2"/><path d="M2.2 4.1l1.3 1.3 2.4-2.6" fill="none" stroke="#fff" stroke-width="1"/></svg>Slower release schedule</li><li><svg viewBox="0 0 8 8"><circle cx="4" cy="4" r="4" fill="#1466c2"/><path d="M2.2 4.1l1.3 1.3 2.4-2.6" fill="none" stroke="#fff" stroke-width="1"/></svg>Limited support hours</li></ul>
          <div class="offer__more">Read More <svg viewBox="0 0 8 8"><circle cx="4" cy="4" r="4" fill="#1466c2"/><path d="M3.2 2.3L5 4 3.2 5.7" fill="none" stroke="#fff" stroke-width="1.1"/></svg></div></div>
        <div class="offer"><svg class="offer__icon" viewBox="0 0 70 66" role="img" aria-label="Hand holding a box with tools icon"><rect x="26" y="6" width="18" height="14" fill="#1466c2"/><rect x="22" y="24" width="30" height="26" fill="#1466c2"/><rect x="8" y="38" width="10" height="22" fill="#1466c2"/><path d="M20 52h34l8-10v14H20z" fill="#1466c2"/></svg><div class="offer__title">Full Service Offering</div>
          <ul class="offer__list"><li><svg viewBox="0 0 8 8"><circle cx="4" cy="4" r="4" fill="#1466c2"/><path d="M2.2 4.1l1.3 1.3 2.4-2.6" fill="none" stroke="#fff" stroke-width="1"/></svg>Mid-range cost per month</li><li><svg viewBox="0 0 8 8"><circle cx="4" cy="4" r="4" fill="#1466c2"/><path d="M2.2 4.1l1.3 1.3 2.4-2.6" fill="none" stroke="#fff" stroke-width="1"/></svg>Releases every 1.5 - 2 months</li><li><svg viewBox="0 0 8 8"><circle cx="4" cy="4" r="4" fill="#1466c2"/><path d="M2.2 4.1l1.3 1.3 2.4-2.6" fill="none" stroke="#fff" stroke-width="1"/></svg>Client can help request</li></ul>
          <div class="offer__more">Read More <svg viewBox="0 0 8 8"><circle cx="4" cy="4" r="4" fill="#1466c2"/><path d="M3.2 2.3L5 4 3.2 5.7" fill="none" stroke="#fff" stroke-width="1.1"/></svg></div></div>
        <div class="offer"><svg class="offer__icon" viewBox="0 0 70 66" role="img" aria-label="Hand holding a crown with people icon"><circle cx="20" cy="14" r="5" fill="#1466c2"/><circle cx="35" cy="8" r="5" fill="#1466c2"/><circle cx="50" cy="14" r="5" fill="#1466c2"/><path d="M22 24l6 6 7-8 7 8 6-6v14H22z" fill="#1466c2"/><path d="M8 52l18-8h30l6-4-12 18H18z" fill="#1466c2"/></svg><div class="offer__title">Premium Service</div>
          <ul class="offer__list"><li><svg viewBox="0 0 8 8"><circle cx="4" cy="4" r="4" fill="#1466c2"/><path d="M2.2 4.1l1.3 1.3 2.4-2.6" fill="none" stroke="#fff" stroke-width="1"/></svg>Higher cost per month</li><li><svg viewBox="0 0 8 8"><circle cx="4" cy="4" r="4" fill="#1466c2"/><path d="M2.2 4.1l1.3 1.3 2.4-2.6" fill="none" stroke="#fff" stroke-width="1"/></svg>Priority 24/7 support</li><li><svg viewBox="0 0 8 8"><circle cx="4" cy="4" r="4" fill="#1466c2"/><path d="M2.2 4.1l1.3 1.3 2.4-2.6" fill="none" stroke="#fff" stroke-width="1"/></svg>Dedicated development lead</li></ul>
          <div class="offer__more">Read More <svg viewBox="0 0 8 8"><circle cx="4" cy="4" r="4" fill="#1466c2"/><path d="M3.2 2.3L5 4 3.2 5.7" fill="none" stroke="#fff" stroke-width="1.1"/></svg></div></div>
      </div>
    </section>
    <section class="cta">
      <h2 class="section-title">Lorem Ipsum Dolor</h2><div class="rule"></div>
      <p class="cta__text">Lorem ipsum dolor sit amet, consectetur adipiscing elit, sed do eiusmod tempor incididunt ut labore et dolore magna aliqua. Ut enim ad minim veniam, quis nostrud exercitation ullamco laboris nisi ut aliquip ex ea commodo consequat. Duis aute irure dolor in reprehenderit in voluptate velit esse cillum dolore fugiat nulla pariatur. Excepteur sint occaecat cupidatat non proident, sunt in culpa qui officia</p>
      <span class="btn">Schedule Free Consultation <svg viewBox="0 0 8 8"><circle cx="4" cy="4" r="4" fill="#fff"/><path d="M3.2 2.3L5 4 3.2 5.7" fill="none" stroke="#1466c2" stroke-width="1.1"/></svg></span>
    </section>
    <footer class="footer">
      <div class="footer__edge"></div>
      <div class="footer__body">
        <div class="brand"><span class="brand__mark"></span><span class="brand__name">Ledgerwise<br>Forge</span></div>
        <p class="footer__about">Ledgerwise Forge adds professionalism to cryptocurrency development.</p>
        <div class="footer__col footer__col--quick"><div class="footer__heading">Quicklinks</div><a>Services</a><a>Ledgerwise Forge Method</a><a>Testimonials</a><a>Blog</a><a>About Us</a></div>
        <div class="footer__col footer__col--other"><div class="footer__heading">Qtherlinks</div><a>Blog</a><a>privacy</a><a>Services</a><a>Team</a></div>
        <div class="footer__col footer__col--news"><div class="footer__heading">Get our Newsletter</div><div class="footer__input">Enter Email:</div><div class="footer__subscribe">Subscribe</div><div class="footer__social"><span></span><span></span><span></span><span></span><span></span></div></div>
        <div class="footer__line"></div>
        <div class="footer__copy">©Copyrights 2021 &nbsp; Ledgerwise Forge &nbsp;| &nbsp; All Rights Reserved &nbsp;|</div>
      </div>
    </footer>
  </div>

</div>
</body>
</html>
```